SkyvornQ Business Cards and Stationary Design

Need a design for our business cards and stationary. I want to carry on the theme of the logo. I want the business cards to have a design on the back. I would like the business cards and the stationary to carry the same theme, design scheme, and branding

Target Market(s)

Airlines and Maintenance Facilities

Industry/Entity Type

Aviation

Contact Information for Business Card

Name
Position Title
Address: 4827 Trellis Hollow Road, Fort Pierce, Florida, 34951
Office Number
Mobile Number
Email
Website

Font styles to use
Serif
Sans Serif

Colors

Designer to choose colors to be used in the design.

```html
<!DOCTYPE html>
<html lang="en">
<head>
<meta charset="utf-8">
<title>SkyvornQ Business Card</title>
<link rel="stylesheet" href="https://fonts.googleapis.com/css2?family=Montserrat:wght@500;600&family=Roboto:wght@400;500&display=swap">
<style>
  :root {
    --bg: #ecebe8;
    --paper: #fbfbfb;
    --navy: #0b2950;
    --navy-deep: #06203f;
    --sky: #2a9fe0;
    --ink: #4a4f57;
    --rule: #233e66;
  }
  * { margin: 0; padding: 0; box-sizing: border-box; }
  html, body { width: 1200px; height: 950px; overflow: hidden; background: var(--bg); }
  .stage { position: relative; width: 1200px; height: 950px; }

  .card {
    position: absolute; left: 300px; width: 600px; height: 345px;
    border-radius: 22px; overflow: hidden;
    box-shadow: 0 2px 8px rgba(0,0,0,.12);
  }
  .card-front { top: 90px; background: var(--paper); }
  .card-back {
    top: 515px;
    background: linear-gradient(200deg, #1a5aa6 0%, var(--navy) 45%, var(--navy-deep) 100%);
  }

  /* front */
  .brand {
    position: absolute; left: 20px; top: 0; width: 280px; height: 345px;
    display: flex; flex-direction: column; align-items: center; justify-content: center; gap: 22px;
  }
  .brand-dot { width: 64px; height: 64px; border-radius: 50%; border: 6px solid var(--sky); }
  .brand-name {
    font-family: "Montserrat", sans-serif; font-weight: 600; font-size: 28px;
    letter-spacing: 5px; color: var(--navy);
  }
  .divider { position: absolute; left: 318px; top: 40px; width: 1.5px; height: 265px; background: var(--rule); }

  .info { position: absolute; left: 345px; top: 44px; width: 230px; font-family: "Roboto", sans-serif; }
  .person { display: flex; gap: 12px; align-items: flex-start; }
  .person svg { margin-top: 4px; }
  .person-name {
    font-family: "Montserrat", sans-serif; font-weight: 500; font-size: 20px;
    letter-spacing: 1.5px; color: var(--navy); line-height: 1.1; white-space: nowrap;
  }
  .person-title {
    font-family: "Montserrat", sans-serif; font-weight: 500; font-size: 15px;
    letter-spacing: 1px; color: var(--sky); margin-top: 3px;
  }
  .info-rule { height: 1.5px; background: var(--rule); margin: 14px 0 16px; }
  .contact { list-style: none; font-size: 13px; color: var(--ink); line-height: 1.55; }
  .contact li { display: flex; gap: 12px; align-items: flex-start; margin-bottom: 6px; }
  .contact svg { flex: none; margin-top: 3px; }
  .contact .lines { display: block; }

  /* back */
  .back-brand { position: absolute; left: 42px; top: 128px; color: #fff; font-family: "Montserrat", sans-serif; }
  .back-name { font-weight: 600; font-size: 28px; letter-spacing: 5px; }
  .back-web { font-weight: 500; font-size: 14px; letter-spacing: 5px; margin-top: 8px; }
  .back-ring {
    position: absolute; left: 320px; top: 38px; width: 270px; height: 270px;
    border-radius: 50%; border: 22px solid #fff;
  }
</style>
</head>
<body>
<main class="stage">

  <section class="card card-front" aria-label="Business card front">
    <div class="brand">
      <span class="brand-dot"></span>
      <span class="brand-name">SKYVORNQ</span>
    </div>

    <div class="divider"></div>

    <div class="info">
      <div class="person">
        <svg width="14" height="16" viewBox="0 0 14 16"><circle cx="7" cy="4" r="3.5" fill="var(--navy)"/><path d="M0 16 Q0 9 7 9 Q14 9 14 16Z" fill="var(--navy)"/></svg>
        <div>
          <div class="person-name">DARA WHITLOW</div>
          <div class="person-title">CEO/FOUNDER</div>
        </div>
      </div>
      <div class="info-rule"></div>
      <ul class="contact">
        <li>
          <svg width="12" height="16" viewBox="0 0 12 16"><path d="M6 0a6 6 0 0 1 6 6c0 4-6 10-6 10S0 10 0 6a6 6 0 0 1 6-6z" fill="var(--navy)"/><circle cx="6" cy="6" r="2.2" fill="#fff"/></svg>
          <span class="lines">4827 Trellis Hollow Road<br>Marlow Bay, Georgia, 31528</span>
        </li>
        <li>
          <svg width="14" height="14" viewBox="0 0 14 14"><path d="M3 0l3 3-2 2c1 2 3 4 5 5l2-2 3 3-2 3C6 14 0 8 0 3z" fill="var(--navy)"/></svg>
          <span>772 514 0386</span>
        </li>
        <li>
          <svg width="14" height="15" viewBox="0 0 12 15"><rect x="1" y="0.5" width="10" height="14" rx="1.5" fill="none" stroke="var(--navy)" stroke-width="1.4"/><circle cx="6" cy="12" r="0.9" fill="var(--navy)"/></svg>
          <span>772 903 6145</span>
        </li>
        <li>
          <svg width="14" height="11" viewBox="0 0 14 11"><rect width="14" height="11" rx="1" fill="var(--navy)"/><path d="M1 1.5l6 4.5 6-4.5" fill="none" stroke="#fff" stroke-width="1.2"/></svg>
          <span>info@skyvornq.com</span>
        </li>
        <li>
          <svg width="14" height="14" viewBox="0 0 14 14"><circle cx="7" cy="7" r="7" fill="var(--navy)"/><path d="M0 7h14M7 0c3 3 3 11 0 14M7 0c-3 3-3 11 0 14" fill="none" stroke="#fff" stroke-width="1"/></svg>
          <span>www.skyvornq.com</span>
        </li>
      </ul>
    </div>
  </section>

  <section class="card card-back" aria-label="Business card back">
    <div class="back-brand">
      <div class="back-name">SKYVORNQ</div>
      <div class="back-web">skyvornq.com</div>
    </div>
    <div class="back-ring"></div>
  </section>

</main>
</body>
</html>
```